Business card for denture clinic Veltrimora

We need a new business card with our new logo. We are a denture clinic in New Zealand with our target market being 45+ years old. We would need a space on the back to write our patients next appointment on. We would space for only one appointment rather than a list. We will attach a photo showing an example of this. But of course, we would like to see your twist on this. We want it to be bold and easy to read and a good mixture of professional but modern. We have attached our logo to be used on the card.

Target Market(s)

People aged 45+ needing dentures

Industry/Entity Type

Dental

Contact Information for Business Card

We want our logo on the front and the space to write an appointment on the back. I've attached an example our our old business card showing this. We need to have the technicians details on the front.

Font styles to use
Sans Serif

Colors
0255a3
919191
fbfbfb

Requirements
Must have
• The following details:
• Liam Dorsett BDT, PGDipCDentTech Calverin
• Dental Prosthetist
• Phone numbers: 0800 47 3125
• 09 572 1394
• Email: liam@veltrimora.co.nz
• www.veltrimora.co.nz
• Address: 14 Marlow Crest Road
• Halbrook West
• Auckland 0793
Nice to have
• We would like our business cards to have more than just two colours as we want them to be more vibrant. We have uploaded an example of a business card we liked that showed this.

```html
<!DOCTYPE html>
<html lang="en">
<head>
<meta charset="utf-8">
<title>Veltrimora – Business Card</title>
<link href="https://fonts.googleapis.com/css2?family=Open+Sans:ital,wght@0,400;0,600;0,700;1,400&display=swap" rel="stylesheet">
<style>
  :root {
    --brand-blue: #0255a3;
    --brand-blue-light: #1f78cc;
    --brand-grey: #919191;
    --paper: #fbfbfb;
    --backdrop: #e6e8eb;
    --ink-soft: #8a8f96;
  }
  * { box-sizing: border-box; margin: 0; padding: 0; }
  html, body {
    width: 1200px; height: 950px; overflow: hidden;
    background: var(--backdrop);
    font-family: "Open Sans", Arial, sans-serif;
  }
  .canvas {
    width: 1200px; height: 950px;
    display: flex; flex-direction: column; align-items: center; justify-content: center;
    gap: 40px;
  }
  .card {
    position: relative;
    width: 740px; height: 423px;
    border-radius: 26px;
    overflow: hidden;
    box-shadow: 0 10px 30px rgba(0,0,0,.18);
  }
  .card-art { position: absolute; inset: 0; width: 100%; height: 100%; }

  /* Brand name */
  .brand {
    position: absolute;
    display: flex; align-items: center; gap: 12px;
  }
  .brand-square { width: 30px; height: 30px; border-radius: 4px; background: var(--brand-blue); }
  .brand-name {
    font-weight: 600; font-size: 38px; letter-spacing: 1px;
    color: var(--brand-blue); text-transform: uppercase; line-height: 1;
  }

  /* Front */
  .card-front { background: var(--paper); }
  .card-front .brand { left: 48px; top: 252px; }

  .contact {
    position: absolute; right: 40px; top: 34px;
    text-align: right; color: #fff;
  }
  .contact-name { font-size: 24px; font-weight: 700; line-height: 1.2; }
  .contact-qual { font-size: 17px; font-weight: 600; line-height: 1.3; }
  .contact-role { font-size: 17px; margin-top: 4px; }
  .contact-address { margin-top: 14px; font-size: 16px; line-height: 1.4; }
  .contact-phones { margin-top: 14px; font-size: 16px; line-height: 1.4; }
  .contact-phones b { font-weight: 700; }
  .contact-web { margin-top: 22px; font-size: 15px; line-height: 1.45; }

  /* Back */
  .card-back { background: linear-gradient(135deg, var(--brand-blue-light), var(--brand-blue)); }
  .field {
    position: absolute; left: -20px;
    width: 330px; height: 58px; border-radius: 29px;
    background: var(--paper);
    display: flex; align-items: center; padding-left: 48px;
    font-style: italic; font-size: 20px; color: var(--ink-soft);
  }
  .field-appointment { top: 120px; }
  .field-time { top: 250px; }
  .card-back .brand { left: 400px; top: 192px; }
  .card-back .brand-square { background: #fff; }
  .card-back .brand-name { color: #fff; }
</style>
</head>
<body>
<main class="canvas">

  <section class="card card-front" aria-label="Card front">
    <svg class="card-art" viewBox="0 0 740 423" aria-hidden="true">
      <path d="M282,0 C352,40 408,90 440,160 C475,240 470,350 545,423" fill="none" stroke="var(--brand-grey)" stroke-width="10" opacity=".55"/>
      <path d="M300,0 H740 V423 H560 C495,350 500,250 462,165 C430,95 375,40 300,0 Z" fill="var(--brand-blue)"/>
    </svg>

    <div class="brand">
      <span class="brand-square"></span>
      <span class="brand-name">Veltrimora</span>
    </div>

    <div class="contact">
      <p class="contact-name">LIAM DORSETT BDT</p>
      <p class="contact-qual">PGDipCDentTech Calverin</p>
      <p class="contact-role">Dental Prosthetist</p>
      <p class="contact-address">14 Marlow Crest Road<br>Halbrook West<br>Auckland 0793</p>
      <p class="contact-phones"><b>P:</b> 0800 47 3125<br><b>C:</b> 09 572 1394</p>
      <p class="contact-web">liam@veltrimora.co.nz<br>www.veltrimora.co.nz</p>
    </div>
  </section>

  <section class="card card-back" aria-label="Card back">
    <div class="field field-appointment">appointment</div>
    <div class="field field-time">time:</div>
    <div class="brand">
      <span class="brand-square"></span>
      <span class="brand-name">Veltrimora</span>
    </div>
  </section>

</main>
</body>
</html>
```